Harborline Auto LLC

Car Dealer Customer Service
Address: 2874 Cresthaven Road, Shelbyville, TN 37162
web: www.harborlineautoxq.net
email: harborlineautoxq@mailnest.example
Phone: (931) 555-0148
Phone: (629) 555-0173

```html
<!DOCTYPE html>
<html lang="en">
<head>
<meta charset="utf-8">
<title>Harborline Auto – Business Card</title>
<link href="https://fonts.googleapis.com/css2?family=Montserrat:wght@500;800&display=swap" rel="stylesheet">
<style>
  :root {
    --brand-blue: #1d7fb5;
    --brand-blue-light: #2b93cf;
    --brand-gold: #ebb243;
    --ink: #1b1b1b;
    --paper: #ffffff;
    --backdrop: #e4e4e4;
  }
  * { box-sizing: border-box; margin: 0; padding: 0; }
  html, body {
    width: 1200px; height: 813px; overflow: hidden;
    background: var(--backdrop);
    font-family: "Montserrat", sans-serif;
  }
  .sheet {
    width: 1200px; height: 813px;
    display: flex; align-items: center; justify-content: center; gap: 36px;
  }
  .card {
    position: relative;
    width: 560px; height: 320px;
    border-radius: 26px;
    border-bottom: 5px solid var(--brand-gold);
    overflow: hidden;
  }
  .card--front { background: var(--paper); }
  .card--back  { background: var(--brand-blue); }

  /* front */
  .front-mark {
    position: absolute; top: 44px; right: 50px;
    display: flex; align-items: center; gap: 12px;
  }
  .mark-dot {
    width: 46px; height: 46px; border-radius: 50%;
    background: var(--brand-gold);
  }
  .front-mark .mark-name {
    font-weight: 800; font-size: 20px; color: var(--brand-blue);
    text-transform: uppercase; letter-spacing: 0.5px;
  }
  .details {
    position: absolute; left: 40px; bottom: 26px;
    color: var(--ink);
  }
  .details .company {
    font-weight: 800; font-size: 26px; color: var(--brand-blue);
    text-transform: uppercase; letter-spacing: 0.5px; margin-bottom: 8px;
  }
  .details .line { font-weight: 500; font-size: 14px; line-height: 19px; }
  .contact-list { list-style: none; margin-top: 10px; }
  .contact-list li {
    display: flex; align-items: center; gap: 10px;
    font-weight: 500; font-size: 14px; line-height: 21px;
  }
  .contact-list svg { width: 14px; height: 14px; fill: var(--brand-blue); flex: none; }

  /* back */
  .back-mark {
    position: absolute; inset: 0;
    display: flex; flex-direction: column; align-items: center; justify-content: center; gap: 22px;
  }
  .back-mark .mark-dot {
    width: 120px; height: 120px;
    background: var(--brand-gold);
  }
  .back-mark .mark-name {
    font-weight: 800; font-size: 40px; color: var(--paper);
    text-transform: uppercase; letter-spacing: 1px;
  }
</style>
</head>
<body>
<main class="sheet">
  <section class="card card--front" aria-label="Card front">
    <div class="front-mark">
      <span class="mark-dot"></span>
      <span class="mark-name">Harborline Auto</span>
    </div>
    <div class="details">
      <h1 class="company">Harborline Auto</h1>
      <p class="line">Car Dealer Customer Service</p>
      <p class="line">2874 Cresthaven Road</p>
      <p class="line">Shelbyville, TN 37162</p>
      <ul class="contact-list">
        <li>
          <svg viewBox="0 0 24 24" aria-hidden="true"><path d="M6.6 10.8a15.1 15.1 0 0 0 6.6 6.6l2.2-2.2a1 1 0 0 1 1-.25 11.4 11.4 0 0 0 3.6.57 1 1 0 0 1 1 1V20a1 1 0 0 1-1 1A17 17 0 0 1 3 4a1 1 0 0 1 1-1h3.5a1 1 0 0 1 1 1c0 1.25.2 2.45.57 3.57a1 1 0 0 1-.25 1z"/></svg>
          (931) 555-0148
        </li>
        <li>
          <svg viewBox="0 0 24 24" aria-hidden="true"><path d="M3 8c0-2 4-4 9-4s9 2 9 4v2h-5V8H8v2H3z"/><rect x="5" y="12" width="14" height="8" rx="2"/></svg>
          (629) 555-0173
        </li>
        <li>
          <svg viewBox="0 0 24 24" aria-hidden="true"><path d="M2 5h20v14H2z M3.5 6.5 12 13l8.5-6.5" stroke="#fff" stroke-width="1.4"/></svg>
          harborlineautoxq@mailnest.example
        </li>
        <li>
          <svg viewBox="0 0 24 24" aria-hidden="true"><circle cx="12" cy="12" r="10"/><path d="M2 12h20M12 2c3 3 3 17 0 20M12 2c-3 3-3 17 0 20" stroke="#fff" stroke-width="1.3" fill="none"/></svg>
          www.harborlineautoxq.net
        </li>
      </ul>
    </div>
  </section>

  <section class="card card--back" aria-label="Card back">
    <div class="back-mark">
      <span class="mark-dot"></span>
      <span class="mark-name">Harborline Auto</span>
    </div>
  </section>
</main>
</body>
</html>
```